Etikett für einen Rosé Wein
Zielgruppe
Wir sind ein Weingut und benötigen ein neues Etikett für unseren Muskattrollinger Rosé. Unsere Kunden sind eher traditionelle Weinkäufer.
Aufgabenstellung
Format:
Höhe: 9 cm
Breite: 11 cm
Da es nur ein Vorderetikett gibt, müssen alle relevanten Angaben (Hersteller, Alkohol, Inhalt in L, Rebsorte, etc.) enthalten sein. (siehe Flaschenabbildung anbei)
WÜRTTEMBERG
2019er
Muskattrollinger Rosé
DEUTSCHER QUALITÄTSWEIN
11,0 % Vol.
0,75 l
Enthält Sulfite
A.P.Nr. 58127364
Abfüller
Straße / PLZ / Ort / Tel.
Der Flaschenverschluss ist schwarz d.h. das neue Etikettendesign sollte dazu passen.
Bisher ist der Hintergrund des Weinetiketts schwarz. Dies muss jedoch nicht so bleiben.
Im Anhang finden Sie außerdem ein Plakat. Ggf. können Sie für das Flaschendesign einige nostalgische Elemente davon übernehmen.

```html
<!DOCTYPE html>
<html lang="de">
<head>
<meta charset="utf-8">
<title>Muskattrollinger Rosé – Etikett</title>
<link rel="stylesheet" href="https://fonts.googleapis.com/css2?family=Playfair+Display:wght@400&family=Pinyon+Script&family=Cormorant+SC:wght@400;500&family=Cormorant+Garamond:wght@400&display=swap">
<style>
  :root {
    --stage: #1a1918;
    --label: #2c2c2e;
    --label-edge: #262628;
    --wine-red: #7d2a3b;
    --ink-light: #ecebea;
    --ink-muted: #b9b8b6;
    --sketch-a: #3b3b3e;
    --sketch-b: #4a4a4d;
  }
  * { margin: 0; padding: 0; box-sizing: border-box; }
  html, body { width: 1200px; height: 1050px; overflow: hidden; background: var(--stage); }
  .canvas { position: relative; width: 1200px; height: 1050px; }
  .label {
    position: absolute; left: 50px; top: 75px; width: 1100px; height: 900px;
    background: linear-gradient(180deg, var(--label) 0%, var(--label-edge) 100%);
    overflow: hidden;
  }
  .region {
    position: absolute; top: 110px; left: 0; width: 100%; text-align: center;
    font-family: "Playfair Display", serif; font-size: 66px; letter-spacing: 2px;
    color: var(--wine-red);
  }
  .landscape {
    position: absolute; left: 40px; top: 330px; width: 1020px; height: 420px;
    border-radius: 40px;
    background: radial-gradient(ellipse at 50% 55%, var(--sketch-b) 0%, var(--sketch-a) 45%, rgba(44,44,46,0) 75%);
    opacity: .8;
  }
  .variety {
    position: absolute; top: 250px; left: 0; width: 100%; text-align: center;
    font-family: "Pinyon Script", cursive; font-size: 112px; line-height: 1.05;
    color: var(--ink-light);
  }
  .variety .style { display: block; margin-left: -120px; }
  .vintage {
    position: absolute; top: 525px; left: 0; width: 100%; text-align: center;
    font-family: "Cormorant SC", serif; font-size: 32px; color: var(--ink-muted);
  }
  .details {
    position: absolute; bottom: 70px; font-family: "Cormorant SC", serif;
    font-size: 28px; line-height: 1.45; color: var(--ink-muted);
  }
  .details--left { left: 60px; }
  .details--right { right: 60px; text-align: right; }
  .quality {
    font-family: "Cormorant Garamond", serif; font-size: 26px; color: var(--wine-red);
    margin-bottom: 8px;
  }
</style>
</head>
<body>
<main class="canvas">
  <section class="label">
    <div class="landscape" role="img" aria-label="Zarte Bleistiftskizze einer Weinberglandschaft mit Rebzeilen, Bäumen und Wolken"></div>
    <h2 class="region">WÜRTTEMBERG</h2>
    <h1 class="variety">Muskattrollinger<span class="style">Rosé</span></h1>
    <p class="vintage">2019er</p>
    <div class="details details--left">
      <p class="quality">Deutscher Qualitätswein</p>
      <p>11,0 % Vol.</p>
      <p>0,75 l</p>
      <p>Enthält Sulfite</p>
    </div>
    <div class="details details--right">
      <p>A.P.Nr. 58127364</p>
      <p>Abfüller</p>
      <p>Straße / PLZ / Ort / Tel.</p>
    </div>
  </section>
</main>
</body>
</html>
```